Brindlemark Group information card

We need a 5x7 two-sided card to hand out at open houses and provide to our charitable partners for distribution. We are a local real estate group looking to add a "give back" component to our business. We are located in a coastal community and would like to incorporate that feel into our design. We are giving clients who use us the ability to designate 1 out of the 10 charitable organizations we partner with - and we will make a donation to that organization.

We included the 10 partner logos below - we envision them pretty small. Also included 2 photos of the "Brindlemark" and our logo. Have fun.
Updates

Target Market(s)

home buyers & sellers

Industry/Entity Type

Real Estate

Font styles to use
Serif
Sans Serif

Colors

Designer to choose colors to be used in the design.

Requirements
Must have
• slogan & tagline - see attached text file
• Brindlemark photo
Nice to have
• partner logos - small - maybe in circles?

```html
<!DOCTYPE html>
<html lang="en">
<head>
<meta charset="utf-8">
<title>Brindlemark Group information card</title>
<link rel="stylesheet" href="https://fonts.googleapis.com/css2?family=Josefin+Sans:wght@400;600&family=Open+Sans:wght@400;600&family=Arimo:wght@400;700&display=swap">
<style>
  :root {
    --page: #eeeeee;
    --white: #ffffff;
    --blue: #5b84c4;
    --blue-mid: #3f5f94;
    --navy: #2d4468;
    --ink: #1c1c1c;
    --black: #0d0d0d;
    --body: #333333;
  }
  * { margin: 0; padding: 0; box-sizing: border-box; }
  html, body { width: 1200px; height: 841px; overflow: hidden; background: var(--page); }
  .stage { position: relative; width: 1200px; height: 841px; }
  .card { position: absolute; top: 123px; height: 601px; background: var(--white); overflow: hidden; box-shadow: 0 2px 6px rgba(0,0,0,.18); }
  .card--front { left: 180px; width: 428px; }
  .card--back { left: 634px; width: 426px; }
  .card svg.art { position: absolute; left: 0; top: 0; }
  .abs { position: absolute; }

  /* front */
  .slogan { left: 30px; top: 14px; font: 400 29px/30px "Josefin Sans", sans-serif; color: var(--blue); letter-spacing: .5px; }
  .brand { font-family: "Open Sans", sans-serif; font-weight: 600; text-align: center; }
  .brand--front { left: 227px; top: 50px; width: 160px; color: var(--white); font-size: 23px; line-height: 27px; }
  .tagline { left: 176px; top: 115px; width: 244px; text-align: right; color: var(--white); font: 400 13px "Open Sans", sans-serif; letter-spacing: -.2px; white-space: nowrap; }
  .pledge { left: 12px; top: 450px; width: 404px; text-align: center; font: 400 13.5px/17px "Arimo", sans-serif; color: var(--ink); }
  .pledge strong { display: block; font-weight: 700; margin-bottom: 4px; }
  .site-bar { left: 0; top: 562px; width: 428px; height: 39px; background: var(--black); color: var(--white); font: 400 14px/39px "Arimo", sans-serif; text-align: center; }

  /* back */
  .brand--back { left: 20px; top: 38px; width: 120px; color: var(--blue-mid); font-size: 19px; line-height: 22px; }
  .headline { left: 158px; top: 28px; font: 600 30px/40px "Josefin Sans", sans-serif; color: var(--blue-mid); letter-spacing: 0; white-space: nowrap; }
  .story { left: 13px; top: 433px; width: 266px; font: 400 8.3px/14px "Open Sans", sans-serif; color: var(--body); text-align: justify; }
  .story p + p { margin-top: 3px; }
  .story .ask { font-size: 10px; margin-top: 5px; }
  .together { left: 300px; top: 429px; width: 122px; text-align: center; font: 600 14.5px/16.5px "Josefin Sans", sans-serif; color: var(--blue); letter-spacing: .4px; }
  .contact-box { left: 304px; top: 520px; width: 122px; height: 81px; background: var(--blue); padding: 4px 0 0 10px; color: var(--navy); }
  .contact-name { font: 600 13px/16px "Open Sans", sans-serif; }
  .contact-mail { font: 400 7.5px/11px "Open Sans", sans-serif; margin-bottom: 9px; }
  .back-bar { left: 0; top: 581px; width: 304px; height: 20px; background: var(--black); }
</style>
</head>
<body>
<main class="stage">

  <section class="card card--front">
    <svg class="art" width="428" height="601" viewBox="0 0 428 601">
      <defs>
        <linearGradient id="sunset" x1="0" y1="0" x2="0" y2="1">
          <stop offset="0" stop-color="#e0786a"/>
          <stop offset=".35" stop-color="#d9857e"/>
          <stop offset=".55" stop-color="#7e6670"/>
          <stop offset=".75" stop-color="#3a3644"/>
          <stop offset="1" stop-color="#2b2a34"/>
        </linearGradient>
      </defs>
      <rect role="img" aria-label="Photo of the coastal town at sunset, the bay and pier under a pink sky" x="0" y="0" width="428" height="405" fill="url(#sunset)"/>
      <polygon points="0,0 235,0 160,140 0,140" fill="var(--white)"/>
      <polygon points="227,15 423,15 423,140 160,140" fill="rgba(58,58,70,.78)"/>
      <polygon points="138,405 236,405 262,440 164,440" fill="var(--navy)"/>
      <polygon points="200,405 298,405 324,440 226,440" fill="var(--blue-mid)"/>
      <polygon points="245,405 428,405 428,440 271,440" fill="var(--blue)"/>
    </svg>
    <h1 class="abs slogan">CHANGE<br>HOMES,<br>CHANGE<br>LIVES</h1>
    <div class="abs brand brand--front">Brindlemark<br>Group</div>
    <p class="abs tagline">Changing the World One Home at a Time</p>
    <p class="abs pledge"><strong>Because we value generosity and desire to make a difference in our community and world,</strong>for every home bought or sold through us, we will make a contribution to one of our amazing partner who are helping to change the world.</p>
    <div class="abs site-bar">www.brindlemarkgroup.com</div>
  </section>

  <section class="card card--back">
    <svg class="art" width="426" height="601" viewBox="0 0 426 601">
      <defs>
        <linearGradient id="coast" x1="0" y1="0" x2="0" y2="1">
          <stop offset="0" stop-color="#8fb3d9"/>
          <stop offset=".4" stop-color="#dfe8f1"/>
          <stop offset=".55" stop-color="#5e8fb5"/>
          <stop offset=".72" stop-color="#8c9078"/>
          <stop offset=".88" stop-color="#6f7a55"/>
          <stop offset="1" stop-color="#a3343a"/>
        </linearGradient>
      </defs>
      <polygon role="img" aria-label="Photo of the coastal town from a hillside, the bay under a blue sky with red flowers in front" points="0,0 426,0 426,140 252,392 0,392" fill="url(#coast)"/>
      <polyline points="0,396 250,396 426,150" fill="none" stroke="var(--blue)" stroke-width="9"/>
      <polyline points="0,408 256,408 426,172" fill="none" stroke="var(--blue)" stroke-width="5"/>
      <g class="partner-badges">
        <circle cx="408" cy="265" r="15" fill="#c9b6c8"/>
        <circle cx="369" cy="311" r="15" fill="#2f3a2f"/>
        <circle cx="407" cy="311" r="15" fill="#6a4a3a"/>
        <circle cx="330" cy="356" r="15" fill="#1b1b1b"/>
        <circle cx="369" cy="356" r="15" fill="#d9e3ee"/>
        <circle cx="407" cy="356" r="15" fill="#d02a2a"/>
        <circle cx="292" cy="401" r="15" fill="#e6e6e6"/>
        <circle cx="330" cy="401" r="15" fill="#e3e6f2"/>
        <circle cx="369" cy="401" r="15" fill="#e07ab0"/>
        <circle cx="407" cy="401" r="15" fill="#2a2a2a"/>
      </g>
    </svg>
    <div class="abs brand brand--back">Brindlemark<br>Group</div>
    <h2 class="abs headline">WE LIVE HERE.<br>WE GIVE HERE.</h2>
    <div class="abs story">
      <p>We give because we value generosity and believe we have been blessed to be a blessing.</p>
      <p>We believe that together we can change the world one home at time. You have our guarantee of personal service and no additional costs. The donations come out of our commission, not your pocket. You get to designate which of our amazing partner organizations you would like us to contribute to on behalf of your transaction. When you are ready to buy or sell, please consider giving us a call.</p>
      <p class="ask">Tell a friend about us too.</p>
    </div>
    <p class="abs together">TOGETHER,<br>WE CAN<br>MAKE THE<br>WORLD A<br>BETTER PLACE.</p>
    <div class="abs contact-box">
      <div class="contact-name">OWEN FALKNER</div>
      <div class="contact-mail">owen@brindlemarkgroup.com</div>
      <div class="contact-name">NORA FALKNER</div>
      <div class="contact-mail">nora@brindlemarkgroup.com</div>
    </div>
    <div class="abs back-bar"></div>
  </section>

</main>
</body>
</html>
```